Sauce business needs a logo design and label design - Re-launching soon

Business based in Chicago, IL. We need a logo design (for Tamsin's Sauces) and a label design for our Sauce product line. We make BBQ Sauces, Marinades, Salad dressings, Burger Sauces, Hot sauces, Ketchup, and Mustards
Our products are named under one brand: Tamsin's Sauces... Each product will have a different name starting with Tamsin's (depending on the flavor of the product). We are looking for a label that will catch consumers eye walking through the store. Our current label doesn't pop enough. We like the colors of Yellow, Red, Orange with a white or black background or any combination thereof.
* Will have to create a label that can be changed to fit particular sauce name and ingredient list, bar codes, etc
Please research designs as we do not want clipart or anything close to any other brands

Target Market(s)

Gourmet foodies, casual consumers,

Industry/Entity Type

Retail

Logo Text

Tamsin's Sauces

Requirements
Must have
• Consistent brand scheme that works for all of my Sauce varieties
Should not have
• Clipart or designs/color schemes from other products/brands

```html
<!DOCTYPE html>
<html lang="en">
<head>
<meta charset="utf-8">
<title>Tamsin's Sauces — Label Range</title>
<link href="https://fonts.googleapis.com/css2?family=Josefin+Sans:wght@400;600;700&family=Playfair+Display:wght@500&family=Yesteryear&family=Oswald:wght@400&family=Lato:wght@300&display=swap" rel="stylesheet">
<style>
  :root {
    --page: #ffffff;
    --label-dark: #2b2b2b;
    --label-dark-mid: #4a4a4a;
    --label-cream: #ece7d5;
    --ink-light: #f1f1ef;
    --ink-dark: #2a2a2a;
    --gold: #d7a53a;
    --red: #a8282a;
    --sage: #8aa07a;
    --leaf: #8ea34e;
    --leaf-band: #87a048;
    --leaf-band-light: #b3c58a;
  }
  * { box-sizing: border-box; margin: 0; padding: 0; }
  html, body {
    width: 1200px; height: 1200px; overflow: hidden;
    background: var(--page);
  }
  .range {
    position: relative; width: 1200px; height: 1200px;
    display: flex; justify-content: center; align-items: center; gap: 40px;
  }
  .label {
    position: relative; width: 350px; height: 560px; overflow: hidden;
    text-align: center;
    background: radial-gradient(ellipse at 50% 45%, var(--label-dark-mid) 0%, var(--label-dark) 75%);
    color: var(--ink-light);
  }
  .label--cream {
    background: radial-gradient(ellipse at 50% 45%, #f3efe2 0%, var(--label-cream) 80%);
    color: var(--ink-dark);
  }
  .label > * { position: absolute; left: 0; right: 0; }
  .brand {
    top: 46px; font-family: "Josefin Sans", sans-serif; font-weight: 600;
    font-size: 40px; letter-spacing: -1px; line-height: 1;
  }
  .product {
    top: 120px; font-family: "Playfair Display", serif; font-weight: 500;
    font-size: 58px; line-height: 1; letter-spacing: -1px; white-space: nowrap;
  }
  .product--gold { color: var(--gold); }
  .product--red { color: var(--red); }
  .product--sage { color: var(--sage); }
  .kind {
    top: 168px; font-family: "Yesteryear", cursive; font-size: 76px; line-height: 1;
  }
  .percent {
    top: 266px; font-family: "Josefin Sans", sans-serif; font-weight: 600; font-size: 16px;
  }
  .natural {
    top: 296px; height: 40px; display: flex; justify-content: center; align-items: center; gap: 12px;
  }
  .natural__text {
    font-family: "Yesteryear", cursive; font-size: 32px; color: var(--leaf); line-height: 1;
  }
  .ribbon { width: 30px; height: 16px; }
  .ingredients { top: 328px; height: 50px; }
  .ingredients svg { display: block; margin: 0 auto; }
  .free-of {
    top: 382px; font-family: "Josefin Sans", sans-serif; font-weight: 700; font-size: 17px;
    letter-spacing: 1px; display: flex; justify-content: center; align-items: center; gap: 10px;
  }
  .free-of__rule { width: 58px; border-top: 1.5px dashed currentColor; opacity: .8; }
  .free-list {
    top: 412px; left: 61px; right: 61px; height: 52px;
    border: 1px solid currentColor; opacity: .95;
    font-family: "Oswald", sans-serif; font-size: 12.5px; letter-spacing: 1.6px;
  }
  .free-list__row { height: 25px; line-height: 25px; }
  .free-list__row + .free-list__row { border-top: 1px solid currentColor; margin: 0 6px; }
  .net {
    top: 474px; font-family: "Yesteryear", cursive; font-size: 25px; line-height: 1;
  }
  .footer-rule { top: 505px; height: 2px; background: var(--ink-light); }
  .label--cream .footer-rule { background: var(--ink-dark); }
  .footer-band {
    top: 512px; bottom: 0;
    background: linear-gradient(90deg, var(--leaf-band-light) 0%, var(--leaf-band) 45%, var(--leaf-band) 70%, #97ad5e 100%);
  }
  .weight {
    top: 515px; left: 120px; right: 120px; height: 27px; line-height: 25px;
    background: #fff; border: 1px solid #555; color: #333;
    font-family: "Lato", sans-serif; font-weight: 300; font-size: 15px;
  }
</style>
</head>
<body>
<main class="range">

  <section class="label label--dark">
    <div class="brand">TAMSIN'S</div>
    <div class="product product--gold">EVERYDAY</div>
    <div class="kind">Sauce</div>
    <div class="percent">• 100% •</div>
    <div class="natural">
      <svg class="ribbon" viewBox="0 0 30 16"><polygon points="0,0 30,0 30,16 0,16 8,8" fill="#f1f1ef"/></svg>
      <span class="natural__text">All Natural</span>
      <svg class="ribbon" viewBox="0 0 30 16"><polygon points="0,0 30,0 22,8 30,16 0,16" fill="#f1f1ef"/></svg>
    </div>
    <div class="ingredients">
      <svg width="120" height="50" viewBox="0 0 120 50">
        <text x="60" y="12" text-anchor="middle" font-size="9" fill="#f1f1ef">★ ★ ★</text>
        <path id="arc-a" d="M14,14 Q60,58 106,14" fill="none"/>
        <text font-family="Josefin Sans, sans-serif" font-weight="600" font-size="11" letter-spacing="1.5" fill="#f1f1ef"><textPath href="#arc-a" startOffset="50%" text-anchor="middle">INGREDIENTS</textPath></text>
      </svg>
    </div>
    <div class="free-of"><span class="free-of__rule"></span>FREE OF<span class="free-of__rule"></span></div>
    <div class="free-list">
      <div class="free-list__row">GLUTEN &nbsp;|&nbsp; GMO &nbsp;|&nbsp; ADDITIVES</div>
      <div class="free-list__row">PRESERVATIVES &nbsp;|&nbsp; COLORING</div>
    </div>
    <div class="net">Net. Weight</div>
    <div class="footer-rule"></div>
    <div class="footer-band"></div>
    <div class="weight">12 oz (355ml)</div>
  </section>

  <section class="label label--dark">
    <div class="brand">TAMSIN'S</div>
    <div class="product product--red">JERK BBQ</div>
    <div class="kind">Sauce</div>
    <div class="percent">• 100% •</div>
    <div class="natural">
      <svg class="ribbon" viewBox="0 0 30 16"><polygon points="0,0 30,0 30,16 0,16 8,8" fill="#f1f1ef"/></svg>
      <span class="natural__text">All Natural</span>
      <svg class="ribbon" viewBox="0 0 30 16"><polygon points="0,0 30,0 22,8 30,16 0,16" fill="#f1f1ef"/></svg>
    </div>
    <div class="ingredients">
      <svg width="120" height="50" viewBox="0 0 120 50">
        <text x="60" y="12" text-anchor="middle" font-size="9" fill="#f1f1ef">★ ★ ★</text>
        <path id="arc-b" d="M14,14 Q60,58 106,14" fill="none"/>
        <text font-family="Josefin Sans, sans-serif" font-weight="600" font-size="11" letter-spacing="1.5" fill="#f1f1ef"><textPath href="#arc-b" startOffset="50%" text-anchor="middle">INGREDIENTS</textPath></text>
      </svg>
    </div>
    <div class="free-of"><span class="free-of__rule"></span>FREE OF<span class="free-of__rule"></span></div>
    <div class="free-list">
      <div class="free-list__row">GLUTEN &nbsp;|&nbsp; GMO &nbsp;|&nbsp; ADDITIVES</div>
      <div class="free-list__row">PRESERVATIVES &nbsp;|&nbsp; COLORING</div>
    </div>
    <div class="net">Net. Weight</div>
    <div class="footer-rule"></div>
    <div class="footer-band"></div>
    <div class="weight">12 oz (355ml)</div>
  </section>

  <section class="label label--cream">
    <div class="brand">TAMSIN'S</div>
    <div class="product product--sage">EVERYDAY</div>
    <div class="kind">Marinade</div>
    <div class="percent">• 100% •</div>
    <div class="natural">
      <svg class="ribbon" viewBox="0 0 30 16"><g stroke="#2a2a2a" stroke-width="1.5"><line x1="4" y1="3" x2="30" y2="3"/><line x1="0" y1="8" x2="30" y2="8"/><line x1="4" y1="13" x2="30" y2="13"/></g></svg>
      <span class="natural__text">All Natural</span>
      <svg class="ribbon" viewBox="0 0 30 16"><g stroke="#2a2a2a" stroke-width="1.5"><line x1="0" y1="3" x2="26" y2="3"/><line x1="0" y1="8" x2="30" y2="8"/><line x1="0" y1="13" x2="26" y2="13"/></g></svg>
    </div>
    <div class="ingredients">
      <svg width="120" height="50" viewBox="0 0 120 50">
        <text x="60" y="12" text-anchor="middle" font-size="9" fill="#2a2a2a">★ ★ ★</text>
        <path id="arc-c" d="M14,14 Q60,58 106,14" fill="none"/>
        <text font-family="Josefin Sans, sans-serif" font-weight="600" font-size="11" letter-spacing="1.5" fill="#2a2a2a"><textPath href="#arc-c" startOffset="50%" text-anchor="middle">INGREDIENTS</textPath></text>
      </svg>
    </div>
    <div class="free-of"><span class="free-of__rule"></span>FREE OF<span class="free-of__rule"></span></div>
    <div class="free-list">
      <div class="free-list__row">GLUTEN &nbsp;|&nbsp; GMO &nbsp;|&nbsp; ADDITIVES</div>
      <div class="free-list__row">PRESERVATIVES &nbsp;|&nbsp; COLORING</div>
    </div>
    <div class="net">Net. Weight</div>
    <div class="footer-rule"></div>
    <div class="footer-band"></div>
    <div class="weight">12 oz (355ml)</div>
  </section>

</main>
</body>
</html>
```